International service dog training school needs web design

We need to upgrade our website. The website is https://brightmeadow.studio/
We help trainers and service dog programs learn how to train service dogs with the latest and most ethical training methods. We offer online and in-person coaching services. We would like to see designs that are engaging and communicate professionalism, expertise, and care for the dogs and people we work with. Please also keep the colors already in the logo in the design.

```html
<!DOCTYPE html>
<html lang="en">
<head>
<meta charset="utf-8">
<title>Helena Marsh Ph.D. – Brightmeadow Institute for Working Dogs</title>
<link rel="stylesheet" href="https://fonts.googleapis.com/css2?family=Rubik:wght@400;500;700&family=Open+Sans:ital,wght@0,400;0,600;0,700;1,400&display=swap">
<style>
:root{
  --teal:#1f9d8e;
  --teal-dark:#167a6f;
  --blue:#1c5fae;
  --blue-deep:#164c92;
  --ink:#111418;
  --text:#4a4f55;
  --white:#ffffff;
  --black:#000000;
  --star:#1c5fae;
}
*{box-sizing:border-box;margin:0;padding:0}
html,body{width:1200px;height:4706px;overflow:hidden}
body{position:relative;background:var(--white);font-family:"Open Sans",Arial,sans-serif;color:var(--text)}
.abs{position:absolute}
.btn{position:absolute;display:flex;align-items:center;justify-content:center;background:var(--teal);color:var(--white);font-family:"Rubik",Arial,sans-serif;font-weight:500;font-size:15px;letter-spacing:.5px;border-radius:30px;text-transform:uppercase}
.h-section{position:absolute;left:0;width:1200px;text-align:center;font-family:"Rubik",Arial,sans-serif;font-weight:500;color:var(--ink);text-transform:uppercase}

/* header */
.site-header{position:absolute;left:0;top:0;width:1200px;height:91px;background:var(--white)}
.brand{position:absolute;left:110px;top:12px;display:flex;align-items:center;gap:10px}
.brand-mark{width:54px;height:54px;border-radius:50%;background:var(--teal)}
.brand-name{font-family:"Rubik",Arial,sans-serif;font-weight:500;color:var(--blue);font-size:21px;line-height:22px}
.brand-name small{display:block;font-size:12.5px;line-height:16px;text-transform:uppercase}
.top-contact{position:absolute;left:652px;top:5px;display:flex;align-items:center;gap:8px;font-size:16px;font-weight:600;color:var(--ink)}
.icon-circle{width:36px;height:36px;border-radius:50%;background:var(--blue);display:flex;align-items:center;justify-content:center}
.socials{position:absolute;left:910px;top:5px;display:flex;gap:9px}
.main-nav{position:absolute;left:452px;top:57px;display:flex;font-family:"Rubik",Arial,sans-serif;font-weight:500;font-size:16px;color:var(--ink)}
.main-nav span{margin-right:31px}
.main-nav span:last-child{margin-right:0}

/* hero */
.hero{position:absolute;left:0;top:91px;width:1200px;height:630px;background:linear-gradient(180deg,#4b6a3a 0%,#6f9a45 45%,#88ad52 100%)}
.hero-shade{position:absolute;left:0;top:0;width:700px;height:630px;background:linear-gradient(90deg,rgba(40,60,30,.45),rgba(40,60,30,0))}
.hero-title{position:absolute;left:118px;top:199px;font-family:"Rubik",Arial,sans-serif;font-weight:700;font-size:45px;line-height:50px;color:var(--white);text-transform:uppercase}
.dots{position:absolute;left:552px;top:581px;display:flex;gap:13px}
.dots i{width:14px;height:14px;border-radius:50%;border:2px solid var(--white)}
.dots i.on{background:var(--white)}

/* about */
.about-quote{position:absolute;left:150px;top:843px;width:900px;text-align:center;font-style:italic;font-size:17px;line-height:30px;color:var(--text)}
.about-photo{position:absolute;left:111px;top:928px;width:459px;height:445px;background:linear-gradient(160deg,#7d7a72,#55524c 60%,#3e3b37)}
.about-text{position:absolute;left:634px;top:924px;width:452px;font-size:13.5px;line-height:30px;text-align:justify}
.about-text p+p{margin-top:7px}

/* services */
.services{position:absolute;left:0;top:1460px;width:1200px;height:1018px;background:linear-gradient(135deg,#1b5eab 0%,#2a73c2 50%,#1a55a0 100%)}
.services-title{position:absolute;left:110px;top:172px;font-family:"Rubik",Arial,sans-serif;font-weight:700;font-size:48px;line-height:48px;color:var(--white);text-transform:uppercase}
.services-intro{position:absolute;left:114px;top:285px;width:290px;font-size:17px;line-height:32px;color:var(--white)}
.card{position:absolute;width:311px;height:404px;background:var(--white);text-align:center}
.card-photo{width:311px;height:210px}
.card h3{margin:18px auto 0;width:250px;font-family:"Rubik",Arial,sans-serif;font-weight:500;font-size:18px;line-height:25px;color:var(--ink)}
.card p{margin:8px auto 0;width:270px;font-size:13.5px;line-height:24px}
.card a{display:inline-block;margin-top:8px;font-family:"Rubik",Arial,sans-serif;font-weight:500;font-size:15px;color:var(--teal);text-decoration:underline}

/* testimonials */
.testi-sub{position:absolute;left:0;top:2604px;width:1200px;text-align:center;font-size:14px;font-weight:600;color:var(--ink)}
.testi{position:absolute;top:2662px;width:320px;text-align:center}
.testi-photo{width:145px;height:145px;border-radius:50%;margin:0 auto}
.stars{margin-top:18px;color:var(--star);font-size:20px;letter-spacing:2px}
.testi p{margin-top:8px;font-style:italic;font-size:13.5px;line-height:26px}
.testi strong{display:block;margin-top:8px;font-family:"Rubik",Arial,sans-serif;font-weight:500;font-size:18px;color:var(--ink)}

/* book */
.book-band{position:absolute;left:0;top:3086px;width:1200px;height:347px;background:linear-gradient(135deg,#1b5eab,#2b78c8 55%,#1a56a2)}
.book{position:absolute;box-shadow:0 8px 20px rgba(0,0,0,.3)}
.book-title{position:absolute;left:504px;top:3160px;font-family:"Rubik",Arial,sans-serif;font-weight:500;font-size:33px;color:var(--white)}
.book-sub{position:absolute;left:504px;top:3226px;font-family:"Rubik",Arial,sans-serif;font-size:26px;line-height:36px;color:var(--white)}

/* events */
.event{position:absolute;left:168px;top:3579px;width:864px;height:378px;background:var(--white);box-shadow:0 2px 12px rgba(0,0,0,.12)}
.event-photo{position:absolute;left:0;top:0;width:413px;height:378px;background:linear-gradient(170deg,#9a9690,#5e5b57 55%,#3c3a38)}
.date-box{position:absolute;left:453px;top:27px;width:66px;height:83px;background:var(--blue);border-radius:4px;color:var(--white);text-align:center;font-family:"Rubik",Arial,sans-serif}
.date-box b{display:block;font-size:40px;line-height:52px;font-weight:500}
.date-box span{font-size:11px;font-weight:700;text-transform:uppercase}
.event h3{position:absolute;left:453px;top:130px;width:340px;font-family:"Rubik",Arial,sans-serif;font-weight:500;font-size:28px;line-height:30px;color:var(--ink)}
.event-meta{position:absolute;left:453px;top:192px;font-size:10.5px;font-weight:600;color:var(--ink);display:flex;align-items:center;gap:4px}
.event p{position:absolute;left:453px;top:222px;width:340px;font-size:13.5px;line-height:24px}

/* cta */
.cta{position:absolute;left:0;top:4041px;width:1200px;height:281px;background:linear-gradient(135deg,#1b5eab,#2a74c4 50%,#1a55a0)}
.cta h2{position:absolute;left:0;top:62px;width:1200px;text-align:center;font-family:"Rubik",Arial,sans-serif;font-weight:500;font-size:37px;color:var(--white)}
.cta p{position:absolute;left:0;top:123px;width:1200px;text-align:center;font-size:18px;color:var(--white)}

/* footer */
.footer{position:absolute;left:0;top:4322px;width:1200px;height:384px;background:var(--black);color:var(--white)}
.footer h4{position:absolute;top:77px;font-family:"Rubik",Arial,sans-serif;font-weight:500;font-size:17px;text-transform:uppercase}
.footer h4::after{content:"";position:absolute;left:0;top:30px;width:32px;height:2px;background:var(--teal)}
.quick{position:absolute;left:413px;top:136px;font-size:14px;line-height:27px}
.contact-row{position:absolute;left:597px;display:flex;align-items:center;gap:12px;font-size:14px;line-height:23px}
.foot-icon{width:34px;height:34px;border-radius:50%;background:var(--teal);display:flex;align-items:center;justify-content:center;flex:none}
.map{position:absolute;left:878px;top:119px;width:210px;height:151px;background:linear-gradient(135deg,#eef0f2,#dfe4e8)}
.copyright{position:absolute;left:0;top:340px;width:1200px;text-align:center;font-size:13px}
</style>
</head>
<body>

<header class="site-header">
  <div class="brand">
    <div class="brand-mark"></div>
    <div class="brand-name">Helena Marsh Ph.D.<small>Brightmeadow Institute<br>for Working Dogs</small></div>
  </div>
  <div class="top-contact">
    <span class="icon-circle"><svg width="18" height="14" viewBox="0 0 18 14"><rect x="1" y="1" width="16" height="12" rx="1.5" fill="none" stroke="#fff" stroke-width="1.8"/><path d="M1 2l8 6 8-6" fill="none" stroke="#fff" stroke-width="1.8"/></svg></span>
    info@brightmeadow.studio
  </div>
  <div class="socials"><span class="icon-circle"></span><span class="icon-circle"></span><span class="icon-circle"></span><span class="icon-circle"></span></div>
  <nav class="main-nav"><span>The Center</span><span>Helping organizations</span><span>Teaching Trainers</span><span>Research</span><span>Contact</span></nav>
</header>

<section class="hero" role="img" aria-label="Photo of a husky puppy sitting on grass beside its trainer holding a teal leash">
  <div class="hero-shade"></div>
  <svg class="abs" style="left:66px;top:300px" width="22" height="34" viewBox="0 0 22 34"><path d="M18 2L4 17l14 15" fill="none" stroke="rgba(255,255,255,.7)" stroke-width="2"/></svg>
  <h1 class="hero-title">Coaching for<br>service dog<br>professionals</h1>
  <div class="btn" style="left:119px;top:376px;width:168px;height:46px">Get started</div>
  <div class="dots"><i></i><i></i><i class="on"></i></div>
</section>

<h2 class="h-section" style="top:800px;font-size:26px">The Brightmeadow Institute for Working Dogs</h2>
<p class="about-quote">“Training service dogs is a rewarding career for those who care about dogs and people. It requires empathy, dedication, precision, and a great deal of knowledge in dog behavior and psychology.”</p>
<div class="about-photo" role="img" aria-label="Photo of trainers with service dogs in vests on a city street"></div>
<div class="about-text">
  <p>The Brightmeadow Institute for Working Dogs was founded by Helena Marsh Ph.D. in response to demand for coaching from dog trainers, medical professionals, and service dog programs. Helena Marsh Ph.D. has helped hundreds of trainers and several programs both in the US and internationally, expand the type of dogs they could offer to include medical alert dogs. Specialized mostly in the training of diabetic alert dogs, seizure dogs, and psychiatric service dogs, Helena Marsh is also experienced in the training of mobility</p>
  <p>assistance dogs and autism dogs. The coaching is individually catered to meet the programs’ needs.</p>
  <p>With a focus on science-based, ethical, and force-free training methods, BIWD provides cutting-edge training</p>
</div>
<div class="btn" style="left:634px;top:1328px;width:169px;height:44px">Learn more</div>

<section class="services">
  <h2 class="services-title">Our<br>services</h2>
  <p class="services-intro">Lorem ipsum dnsectetur adipiscing elit, sed do eiusmod por incididunt ut labore magna aliqua. Quis ipsum supendisse ultrices gravida. Risus commodo viverra maecenas</p>

  <article class="card" style="left:444px;top:92px">
    <div class="card-photo" role="img" aria-label="Group photo of program staff with their dogs" style="background:linear-gradient(180deg,#8a8f98,#4f5a6e)"></div>
    <h3>Organization/Program Consulting</h3>
    <p>Helping organizations get started, improve their training program, and add services</p>
    <a>LEARN MORE »</a>
  </article>
  <article class="card" style="left:778px;top:92px">
    <div class="card-photo" role="img" aria-label="Trainer working with a dog indoors" style="background:linear-gradient(180deg,#c9c4bc,#6b6660)"></div>
    <h3>Professional coaching/ teaching for dog trainers</h3>
    <p>Helping dog trainers improve their skills and learn about service dog training and medical alert dog training.</p>
    <a>LEARN MORE »</a>
  </article>
  <article class="card" style="left:111px;top:519px">
    <div class="card-photo" role="img" aria-label="Dog sniffing scent cans on a tiled floor" style="background:linear-gradient(180deg,#b9b6b0,#7e7a74)"></div>
    <h3>Collaborating in Research Projects</h3>
    <p>Collaborating in research studies in the field of Medical Detection Dogs.</p>
    <a>LEARN MORE »</a>
  </article>
  <article class="card" style="left:444px;top:519px">
    <div class="card-photo" role="img" aria-label="Audience at a seminar presentation" style="background:linear-gradient(180deg,#7d4b3e,#3e3232)"></div>
    <h3>Presentations and Seminars</h3>
    <p>Sharing knowledge about service dogs and medical detection.</p>
    <a>LEARN MORE »</a>
  </article>
  <article class="card" style="left:778px;top:519px">
    <div class="card-photo" role="img" aria-label="Service dog in a red vest at an airport window" style="background:linear-gradient(180deg,#c8ccd0,#5b4a42)"></div>
    <h3>International Services</h3>
    <p>Fluent in both English and French, in-person and online coaching around the world.</p>
    <a>LEARN MORE »</a>
  </article>
</section>

<h2 class="h-section" style="top:2555px;font-size:32px">Testimonials</h2>
<p class="testi-sub">ed ut perspiciatis unde omnis iste natus error sit voluptatem accusantium doloremque</p>
<div class="testi" style="left:103px">
  <div class="testi-photo" role="img" aria-label="Portrait of a schnauzer" style="background:radial-gradient(circle,#8b8b88,#4d6a3c)"></div>
  <div class="stars">★★★★★</div>
  <p>Lorem ipsum dolor sit amet, consedrfrdctetur adipiscing elit, sed do eiuod tempor incididunt ut labore et dolore iua. Quis ipsum suspendisse ultrices gravida.</p>
  <strong>- John Smith</strong>
</div>
<div class="testi" style="left:441px">
  <div class="testi-photo" role="img" aria-label="Portrait of a small white terrier" style="background:radial-gradient(circle,#e8e4dc,#8a9a80)"></div>
  <div class="stars">★★★★★</div>
  <p>Lorem ipsum dolor sit amet, consedrfrdctetur adipiscing elit, sed do eiuod tempor incididunt ut labore et dolore iua. Quis ipsum suspendisse ultrices gravida.</p>
  <strong>- John Smith</strong>
</div>
<div class="testi" style="left:777px">
  <div class="testi-photo" role="img" aria-label="Portrait of a Jack Russell terrier" style="background:radial-gradient(circle,#d9a878,#5f7a3e)"></div>
  <div class="stars">★★★★★</div>
  <p>Lorem ipsum dolor sit amet, consedrfrdctetur adipiscing elit, sed do eiuod tempor incididunt ut labore et dolore iua. Quis ipsum suspendisse ultrices gravida.</p>
  <strong>- John Smith</strong>
</div>

<section class="book-band"></section>
<div class="book" role="img" aria-label="Book cover with a retriever service dog" style="left:110px;top:3091px;width:213px;height:324px;background:linear-gradient(180deg,#f3efe8 0%,#e8dcc8 55%,#b8322e 100%)"></div>
<div class="book" role="img" aria-label="Book cover shown at an angle" style="left:262px;top:3050px;width:200px;height:315px;transform:rotate(12deg);background:linear-gradient(180deg,#f5f1ea 0%,#e6d6bd 55%,#b8322e 100%)"></div>
<h2 class="book-title">New book from Helena Marsh ph.D.!</h2>
<p class="book-sub">Partnering With Your Working Dog:<br>A Calm Guide to Life in Public Places</p>
<div class="btn" style="left:504px;top:3309px;width:170px;height:46px">Learn more</div>

<h2 class="h-section" style="top:3510px;font-size:32px">Latest events</h2>
<article class="event">
  <div class="event-photo" role="img" aria-label="Instructor addressing seated seminar attendees"></div>
  <div class="date-box"><b>18</b><span>March</span></div>
  <h3>Canine Cognition Testing Seminar</h3>
  <div class="event-meta">
    <svg width="10" height="10" viewBox="0 0 10 10"><circle cx="5" cy="5" r="4" fill="none" stroke="#111" stroke-width="1.4"/><path d="M5 2.5V5h2" stroke="#111" stroke-width="1.2" fill="none"/></svg>9:00 AM - 5:00 PM
    <svg width="8" height="11" viewBox="0 0 8 11"><path d="M4 0a4 4 0 0 0-4 4c0 3 4 7 4 7s4-4 4-7a4 4 0 0 0-4-4z" fill="#111"/></svg>4415 LINDEN PARK RD. COLUMBUS OH 43214
  </div>
  <p>Learn from scent detection expert Owen Harlow, how cognition tests can help you improve your results.</p>
  <div class="btn" style="left:456px;top:305px;width:170px;height:46px">Learn more</div>
</article>

<section class="cta">
  <h2>STAYING AHEAD</h2>
  <p>Science-based and ethical training methods for the modern service dog trainer.</p>
  <div class="btn" style="left:517px;top:168px;width:168px;height:46px">Get started</div>
</section>

<footer class="footer">
  <div class="brand" style="top:70px">
    <div class="brand-mark" style="width:46px;height:46px"></div>
    <div class="brand-name" style="color:var(--teal);font-size:19px">Helena Marsh Ph.D.<small>Brightmeadow Institute<br>for Working Dogs</small></div>
  </div>
  <div class="abs" style="left:157px;top:160px;display:flex;gap:16px">
    <span class="icon-circle" style="width:28px;height:28px"></span><span class="icon-circle" style="width:28px;height:28px;background:#c2185b"></span><span class="icon-circle" style="width:28px;height:28px"></span><span class="icon-circle" style="width:28px;height:28px"></span>
  </div>
  <h4 style="left:413px">Quick links</h4>
  <div class="quick">BIWD<br>The Center<br>Helping organizations<br>Teaching Trainers<br>Research Contact</div>
  <h4 style="left:597px">Contact details</h4>
  <div class="contact-row" style="top:126px"><span class="foot-icon"><svg width="12" height="16" viewBox="0 0 12 16"><path d="M6 0a6 6 0 0 0-6 6c0 4.5 6 10 6 10s6-5.5 6-10a6 6 0 0 0-6-6zm0 8.5a2.5 2.5 0 1 1 0-5 2.5 2.5 0 0 1 0 5z" fill="#fff"/></svg></span>4415 Linden Park Rd<br>Columbus OH 43214</div>
  <div class="contact-row" style="top:198px"><span class="foot-icon"><svg width="15" height="15" viewBox="0 0 15 15"><path d="M3 1l2.5 3-1.3 1.6a8 8 0 0 0 5.2 5.2L11 9.5l3 2.5-1.6 2A11 11 0 0 1 1 2.6z" fill="#fff"/></svg></span>(555) 014 – 2287</div>
  <div class="contact-row" style="top:250px"><span class="foot-icon"><svg width="15" height="12" viewBox="0 0 18 14"><rect x="1" y="1" width="16" height="12" rx="1.5" fill="none" stroke="#fff" stroke-width="1.8"/><path d="M1 2l8 6 8-6" fill="none" stroke="#fff" stroke-width="1.8"/></svg></span>info@brightmeadow.studio</div>
  <h4 style="left:878px">Location map</h4>
  <div class="map" role="img" aria-label="Street map showing the office location"></div>
  <p class="copyright">Copyright © 2021 Brightmeadow. All rights reserved.</p>
</footer>

</body>
</html>
```